RVT Business Card Design

We are an independent auto dealer who specializes in commercial & fleet vehicles, we are family owned and operated and have been in business since 2001. We stock late model, low mileage, white trucks & vans. We mostly deal with companies in the construction and service industries. We are just looking to try to freshen up our old business card, we do not want to change the logo at this point, because it is well know within the southwest region & construction community. I have attached our logo and a PDF of our current business card for reference.
Updates
If the address is stacked there is no comma (,) after NE. Everyone keeps putting it in with this format and it is not correct.
482 Morrow Ave NE
Albuquerque, NM 87107
If the address is all on one line, then there will be a comma (,) after NE
482 Morrow Ave NE, Albuquerque, NM 87107
Please make changes accordingly, thank you for your attention in this matter.
Industry/Entity Type
Construction
Contact Information for Business Card
482 Morrow Ave NE, Albuquerque, NM 87107, Dorian Pellew, Vice President, dorian@rvtfleetcars.example, www.RVTfleetcars.example, ph 505-218-4470, fax 505-627-1904, cell 505-763-2085
Look and feel

```html
<!DOCTYPE html>
<html lang="en">
<head>
<meta charset="utf-8">
<title>RVT Auto Sales – Business Card</title>
<link href="https://fonts.googleapis.com/css2?family=Arimo:wght@400;700&family=Open+Sans:ital,wght@0,400;0,600;1,400&display=swap" rel="stylesheet">
<style>
  :root {
    --page: #e9e9eb;
    --card-white: #ffffff;
    --card-fade: #e4e4e6;
    --charcoal: #2f2d2e;
    --charcoal-light: #4a4748;
    --red: #e8202a;
    --red-deep: #b5121b;
    --ink: #2a2a2a;
    --light-text: #d6d6d6;
  }
  * { margin: 0; padding: 0; box-sizing: border-box; }
  html, body { width: 1200px; height: 900px; overflow: hidden; background: var(--page); }
  .canvas { position: relative; width: 1200px; height: 900px; display: flex; align-items: center; justify-content: center; }
  .card {
    position: relative; width: 1050px; height: 600px; overflow: hidden;
    background: linear-gradient(180deg, var(--card-white) 0%, var(--card-fade) 100%);
    box-shadow: 0 10px 30px rgba(0,0,0,.18);
    font-family: "Open Sans", sans-serif;
  }
  .card__wave { position: absolute; inset: 0; width: 100%; height: 100%; }
  .brand { position: absolute; left: 56px; top: 54px; }
  .brand__row { display: flex; align-items: center; gap: 14px; }
  .brand__mark { width: 22px; height: 22px; background: var(--red); }
  .brand__name {
    font-family: "Open Sans", sans-serif; font-weight: 600; font-size: 58px;
    line-height: 1; color: var(--ink); letter-spacing: 1px;
  }
  .brand__tagline { margin-top: 10px; font-size: 16px; font-style: italic; color: #555; }
  .brand__division { margin-top: 12px; font-size: 25px; color: var(--ink); }
  .person { position: absolute; right: 60px; top: 150px; text-align: left; font-family: "Arimo", sans-serif; }
  .person__name { font-size: 46px; font-weight: 700; color: var(--red); letter-spacing: 2px; word-spacing: 10px; }
  .person__title { margin-top: 4px; padding-left: 50px; font-size: 32px; color: var(--ink); letter-spacing: 1px; word-spacing: 6px; }
  .address { position: absolute; left: 52px; top: 330px; font-size: 27px; line-height: 1.42; color: var(--light-text); }
  .contacts { position: absolute; right: 60px; bottom: 36px; font-size: 28px; color: var(--light-text); }
  .contacts__row { display: grid; grid-template-columns: 110px 30px auto; line-height: 1.45; }
  .contacts__label { font-weight: 600; }
</style>
</head>
<body>
<main class="canvas">
  <article class="card">
    <svg class="card__wave" viewBox="0 0 1050 600" preserveAspectRatio="none" aria-hidden="true">
      <defs>
        <linearGradient id="ribbon" x1="0" y1="0" x2="1" y2="0">
          <stop offset="0" stop-color="var(--red-deep)"/>
          <stop offset="1" stop-color="var(--red)"/>
        </linearGradient>
        <linearGradient id="band" x1="0" y1="0" x2="0" y2="1">
          <stop offset="0" stop-color="var(--charcoal-light)"/>
          <stop offset="1" stop-color="var(--charcoal)"/>
        </linearGradient>
      </defs>
      <path d="M0,262 C300,210 620,300 1050,398 L1050,478 C620,352 300,232 0,272 Z" fill="url(#ribbon)"/>
      <path d="M0,272 C300,232 620,352 1050,478 L1050,600 L0,600 Z" fill="url(#band)"/>
    </svg>

    <header class="brand">
      <div class="brand__row">
        <span class="brand__mark"></span>
        <span class="brand__name">RVT AUTO SALES</span>
      </div>
      <p class="brand__tagline">Specializing in Commercial &amp; Fleet Vehicles</p>
      <p class="brand__division">A Division of RV Torque Mechanical Inc</p>
    </header>

    <section class="person">
      <h1 class="person__name">Dorian Pellew</h1>
      <p class="person__title">Vice President</p>
    </section>

    <address class="address" style="font-style:normal">
      482 Morrow Ave NE<br>
      Albuquerque, NM 87107<br>
      www.RVTfleetcars.example<br>
      dorian@rvtfleetcars.example
    </address>

    <section class="contacts">
      <div class="contacts__row"><span class="contacts__label">Phone</span><span>:</span><span>505-218-4470</span></div>
      <div class="contacts__row"><span class="contacts__label">Cell</span><span>:</span><span>505-763-2085</span></div>
      <div class="contacts__row"><span class="contacts__label">Fax</span><span>:</span><span>505-627-1904</span></div>
    </section>
  </article>
</main>
</body>
</html>
```